LEARN Business Skills so you can Earn a good living

size of the poster is 8”x 10.75" plus 0.25" bleed.
Please leave 1 inch on the bottoum for footer
I want a design a poster that will attract people's attention.
I appreciate a creative ad however the ad should not take away from being able to clearly read the text.
-I also appreciate a simple creative ad that is not too busy.
-you can use graphics, vectors, or pictures of real people.
-however, if you use real people it should be a white male that is wearing a white shirt and look like a professional person.

Target Market(s)

Potential young business people

Industry/Entity Type

education

Requirements
Must have
• easy to read the text
Nice to have
• I would like a "creative" simple ad that is easy to be read
Should not have
• pictures of women

```html
<!DOCTYPE html>
<html lang="en">
<head>
<meta charset="UTF-8">
<title>Learn It To Earn It – Business Enrichment Course</title>
<link href="https://fonts.googleapis.com/css2?family=Poppins:wght@300;400;500;600;700;800;900&display=swap" rel="stylesheet">
<style>
  :root{
    --ink:#1c1c1c;
    --band:#262626;
    --paper:#ffffff;
    --rule:#b9b9b9;
    --icon:#6a6a6a;
    --muted:#e6e6e6;
  }
  *{margin:0;padding:0;box-sizing:border-box;}
  html,body{width:800px;height:1200px;overflow:hidden;background:var(--paper);}
  body{font-family:'Poppins',sans-serif;color:var(--ink);}
  .poster{position:relative;width:800px;height:1200px;overflow:hidden;background:var(--paper);}

  .office-photo{position:absolute;left:0;top:0;width:800px;height:814px;
    background:linear-gradient(100deg,#ffffff 0%,#f4f4f4 35%,#e9e9e9 60%,#dcdcdc 100%);}
  .model-photo{position:absolute;left:452px;top:168px;width:348px;height:646px;
    border-radius:150px 150px 0 0;
    background:linear-gradient(180deg,#cfcfcf 0%,#ececec 30%,#e2e2e2 70%,#7a7a7a 100%);}

  .headline{position:absolute;left:40px;top:52px;line-height:1;}
  .headline .learn{font-weight:900;font-size:172px;letter-spacing:-5px;}
  .headline .thin{font-weight:300;}
  .headline .line-one{display:block;white-space:nowrap;}
  .headline .line-one .thin{font-size:172px;letter-spacing:-4px;margin-left:14px;}
  .headline .line-two{display:block;white-space:nowrap;font-size:104px;margin-top:-8px;letter-spacing:-3px;}
  .headline .line-two .bold{font-weight:800;}

  .rule{position:absolute;height:1px;background:var(--rule);}
  .rule.top{left:45px;top:362px;width:445px;}
  .rule.mid{left:45px;top:610px;width:445px;}

  .course-title{position:absolute;left:42px;top:388px;font-weight:800;font-size:60px;line-height:66px;letter-spacing:-0.5px;}
  .tagline{position:absolute;left:44px;top:628px;font-weight:600;font-size:34px;line-height:44px;letter-spacing:-0.3px;}

  .band{position:absolute;left:0;top:814px;width:800px;height:386px;background:var(--band);}
  .skills-frame{position:absolute;left:54px;top:884px;width:692px;height:178px;border:1.5px solid #d9d9d9;border-radius:20px;}
  .skills-title{position:absolute;left:96px;top:858px;width:606px;height:51px;background:var(--paper);border-radius:26px;
    font-weight:700;font-size:30px;line-height:51px;text-align:center;color:var(--ink);letter-spacing:0.3px;}
  .divider{position:absolute;top:924px;width:1px;height:120px;background:#6a6a6a;}
  .skill{position:absolute;top:924px;width:220px;text-align:center;color:var(--paper);}
  .skill svg{display:block;margin:0 auto;}
  .skill p{font-weight:600;font-size:21px;line-height:27px;margin-top:8px;}

  .topics{position:absolute;left:30px;top:1086px;width:740px;text-align:center;color:var(--paper);
    font-size:12.5px;line-height:16.5px;font-weight:400;letter-spacing:0.1px;}
</style>
</head>
<body>
<main class="poster">
  <div class="office-photo" role="img" aria-label="Softly blurred bright office interior in black and white"></div>
  <div class="model-photo" role="img" aria-label="Smiling young businessman in glasses, white shirt and dark tie, holding a folder"></div>

  <h1 class="headline">
    <span class="line-one"><span class="learn">LEARN</span><span class="thin">IT</span></span>
    <span class="line-two"><span class="thin">TO </span><span class="bold">EARN</span><span class="thin"> IT</span></span>
  </h1>

  <div class="rule top"></div>
  <h2 class="course-title">BUSINESS<br>ENRICHMENT<br>COURSE</h2>
  <div class="rule mid"></div>
  <p class="tagline">A proven success of<br>helping people in their<br>livelihoods</p>

  <section class="band"></section>
  <div class="skills-frame"></div>
  <div class="skills-title">BUSINESS SKILLS THAT WILL HELP YOU</div>
  <div class="divider" style="left:283px"></div>
  <div class="divider" style="left:516px"></div>

  <div class="skill" style="left:71px">
    <svg width="62" height="62" viewBox="0 0 62 62" aria-hidden="true">
      <circle cx="31" cy="31" r="29" fill="var(--icon)" stroke="#fff" stroke-width="1.5"/>
      <rect x="20" y="17" width="22" height="16" rx="2" fill="none" stroke="#fff" stroke-width="1.5"/>
      <circle cx="31" cy="37" r="6" fill="none" stroke="#fff" stroke-width="1.5"/>
      <path d="M27 42 L25 49 L31 46 L37 49 L35 42" fill="none" stroke="#fff" stroke-width="1.5"/>
    </svg>
    <p>Get a<br>quality job</p>
  </div>
  <div class="skill" style="left:290px">
    <svg width="62" height="62" viewBox="0 0 62 62" aria-hidden="true">
      <circle cx="31" cy="31" r="29" fill="var(--icon)" stroke="#fff" stroke-width="1.5"/>
      <rect x="17" y="36" width="5" height="8" fill="none" stroke="#fff" stroke-width="1.4"/>
      <rect x="25" y="32" width="5" height="12" fill="none" stroke="#fff" stroke-width="1.4"/>
      <rect x="33" y="28" width="5" height="16" fill="none" stroke="#fff" stroke-width="1.4"/>
      <rect x="41" y="22" width="5" height="22" fill="none" stroke="#fff" stroke-width="1.4"/>
      <path d="M16 30 L26 24 L32 26 L44 17 M39 17 H44 V22" fill="none" stroke="#fff" stroke-width="1.5"/>
    </svg>
    <p>Start/grow<br>your business</p>
  </div>
  <div class="skill" style="left:524px">
    <svg width="62" height="62" viewBox="0 0 62 62" aria-hidden="true">
      <circle cx="31" cy="31" r="29" fill="var(--icon)" stroke="#fff" stroke-width="1.5"/>
      <rect x="18" y="30" width="26" height="14" rx="1.5" fill="none" stroke="#fff" stroke-width="1.5"/>
      <circle cx="31" cy="37" r="3.5" fill="none" stroke="#fff" stroke-width="1.4"/>
      <path d="M18 26 H40 M18 23 H36" stroke="#fff" stroke-width="1.4"/>
      <path d="M24 21 L32 15 L36 18 L44 12 M40 12 H44 V16" fill="none" stroke="#fff" stroke-width="1.5"/>
    </svg>
    <p>Increase your<br>salary</p>
  </div>

  <p class="topics">
    BUSINESS ADMINISTRATION &nbsp;|&nbsp; SMALL BUSINESS MANAGEMENT &nbsp;|&nbsp; FINANCE | INVESTMENTS &nbsp;|&nbsp; COMPUTERS &nbsp;|&nbsp; ACCOUNTING<br>
    SALES &nbsp;|&nbsp; MARKETING &nbsp;|&nbsp; PROJECT MANAGEMENT INTERVIEWING SKILLS &nbsp;|&nbsp; BUSINESS LAW &nbsp;|&nbsp; NEGOTIATION &nbsp;|&nbsp; PUBLIC SPEAKING<br>
    IMPORT/EXPORT &nbsp;|&nbsp; INFORMATION TECHNOLOGY &nbsp;|&nbsp; DISTRIBUTION &nbsp;|&nbsp; MARKETING &nbsp;|&nbsp; LEDGERLY &nbsp;|&nbsp; REAL ESTATE<br>
    HEALTH CARE-MANAGEMENT &nbsp;|&nbsp; RIVERMART
  </p>
</main>
</body>
</html>
```